Venture 482 - Lumora Book Cover

I am looking for a Lumora book cover for my book about "Venture 482".
The Book is Titled:
Venture 482 Ascended
Shaping Outcomes: Paths To Unlocking Cosmic Truths
Author is Dorian Pell
Here is a book description that may help you understand more about it:
Inspired by the genius of Edwin Marlowe, this comprehensive guide delves into the ancient wisdom and cutting-edge science behind the 482 method, a powerful tool for manifesting your desires. Whether you're seeking personal growth, financial success, or spiritual enlightenment, this book provides advanced techniques and methods to transform your dreams into reality.
Any questions please ask.
Thanks
Owen

```html
<!DOCTYPE html>
<html lang="en">
<head>
<meta charset="utf-8">
<title>Venture 482 Ascended — Dorian Pell</title>
<link rel="stylesheet" href="https://fonts.googleapis.com/css2?family=Bebas+Neue&family=Varela+Round&family=Tinos:wght@400;700&family=Cormorant+Garamond:wght@500&display=swap">
<style>
  :root {
    --backdrop: #ececec;
    --cover-top: #e4e4e4;
    --cover-bottom: #b8b8b8;
    --navy: #25223f;
    --indigo: #3b3c86;
    --ink: #111111;
    --emblem-light: #f4f4f4;
    --emblem-mid: #bdbdbd;
    --emblem-dark: #6d6d6d;
  }
  * { margin: 0; padding: 0; box-sizing: border-box; }
  html, body {
    width: 1200px;
    height: 1131px;
    overflow: hidden;
    background: var(--backdrop);
  }
  .book-cover {
    position: absolute;
    left: 245px;
    top: 30px;
    width: 710px;
    height: 1071px;
    overflow: hidden;
    background: radial-gradient(ellipse at 50% 5%, #f2f2f2 0%, var(--cover-top) 30%, var(--cover-bottom) 100%);
    text-align: center;
  }
  .title-main {
    position: absolute;
    top: 82px;
    left: 0;
    width: 100%;
    font-family: "Bebas Neue", "Oswald", sans-serif;
    font-size: 176px;
    line-height: 1;
    letter-spacing: 2px;
    color: var(--navy);
  }
  .emblem {
    position: absolute;
    left: 92px;
    top: 215px;
    width: 520px;
    height: 520px;
  }
  .emblem-number {
    position: absolute;
    left: 0;
    top: 430px;
    width: 100%;
    font-family: "Varela Round", "Arial Rounded MT Bold", sans-serif;
    font-size: 98px;
    line-height: 1;
    color: var(--ink);
    transform: translateX(-3px);
  }
  .title-sub {
    position: absolute;
    top: 718px;
    left: 0;
    width: 100%;
    padding-left: 28px;
    font-family: "Bebas Neue", "Oswald", sans-serif;
    font-size: 60px;
    line-height: 1;
    letter-spacing: 0.92em;
    color: var(--navy);
  }
  .subtitle {
    position: absolute;
    top: 808px;
    left: 0;
    width: 100%;
    font-family: "Tinos", "Times New Roman", serif;
    color: var(--indigo);
    font-size: 25px;
    line-height: 32px;
  }
  .subtitle-lead {
    display: block;
    font-weight: 700;
    text-transform: uppercase;
    letter-spacing: -0.3px;
  }
  .author {
    position: absolute;
    top: 990px;
    left: 0;
    width: 100%;
    padding-left: 40px;
    font-family: "Cormorant Garamond", "Times New Roman", serif;
    font-weight: 500;
    font-size: 54px;
    line-height: 1;
    letter-spacing: 0.38em;
    color: var(--ink);
    text-transform: uppercase;
  }
</style>
</head>
<body>
  <main class="book-cover">
    <h1 class="title-main">Venture</h1>

    <svg class="emblem" viewBox="0 0 520 520" role="img" aria-label="Sacred geometry mandala illustration with concentric circles, petals and radiating markers">
      <defs>
        <radialGradient id="emblem-fill" cx="50%" cy="50%" r="50%">
          <stop offset="0%" stop-color="var(--emblem-light)"/>
          <stop offset="45%" stop-color="var(--emblem-mid)"/>
          <stop offset="80%" stop-color="var(--emblem-dark)" stop-opacity="0.55"/>
          <stop offset="100%" stop-color="var(--emblem-dark)" stop-opacity="0"/>
        </radialGradient>
      </defs>
      <circle cx="260" cy="260" r="258" fill="url(#emblem-fill)"/>
    </svg>
    <div class="emblem-number">482</div>

    <h2 class="title-sub">Ascended</h2>

    <p class="subtitle">
      <span class="subtitle-lead">Shaping Outcomes:</span>
      Paths to unlocking<br>cosmic truths
    </p>

    <p class="author">Dorian Pell</p>
  </main>
</body>
</html>
```